****Business Card Design for Quarrystone Development. Design based around attached logo/company name

I’m looking for business card design for my company Quarrystone Development Group,LLC. Design should be professional, sharp and minimal. Outside of the attached logos, greyscale colors for remainder of cards. My thoughts are two-sided card with attached logo on one side and my info on the other but open to one-sided as well with right design.
Target Market(s)
Real estate professionals including banks, private investors, property owners, developers, commercial tenants like Brewlantern, Grovika or Tanquist’s.
Industry/Entity Type
Commercial real estate development and investments.
Contact Information for Business Card
Name, title, email, phone #’s, web address and physical address
Font styles to use
Other font styles liked:
- Helvetica, Garamond, etc
Colors
Designer to choose only greyscale colors for use in the design.
Requirements
Must have
- Attached logo first or second options.
Nice to have
- Two sided card with logo on one side. Attached Logo/company name can be laid out any way that flows as long as it’s legible.name
Should not have
- No loud colors. ***Please do not include logo, I have removed the company design with a logo image.

```html
<!DOCTYPE html>
<html lang="en">
<head>
<meta charset="utf-8">
<title>Quarrystone Development Group, LLC — Business Card</title>
<link href="https://fonts.googleapis.com/css2?family=Arimo:wght@400&family=Libre+Baskerville:wght@700&display=swap" rel="stylesheet">
<style>
  :root {
    --backdrop: #2e2e30;
    --panel-slate: #5b6577;
    --card-white: #ffffff;
    --name-slate: #4f5a6c;
    --text-grey: #8a8a8e;
    --icon-grey: #5f6470;
  }
  * { box-sizing: border-box; margin: 0; padding: 0; }
  html, body {
    width: 1200px;
    height: 901px;
    overflow: hidden;
    background: var(--backdrop);
  }
  .business-card {
    position: absolute;
    left: 150px;
    top: 193px;
    width: 900px;
    height: 514px;
    display: flex;
    background: var(--card-white);
    box-shadow: 0 14px 30px rgba(0, 0, 0, 0.45);
  }
  .brand-panel {
    width: 380px;
    height: 100%;
    background: var(--panel-slate);
    display: flex;
    align-items: center;
    justify-content: center;
    padding: 0 40px 60px;
  }
  .brand-name {
    font-family: "Arimo", Helvetica, Arial, sans-serif;
    font-weight: 400;
    font-size: 26px;
    line-height: 1.35;
    color: var(--card-white);
    text-align: center;
  }
  .contact-panel {
    flex: 1;
    padding: 150px 0 0 50px;
    font-family: "Arimo", Helvetica, Arial, sans-serif;
    color: var(--text-grey);
  }
  .person-name {
    font-family: "Libre Baskerville", Georgia, serif;
    font-weight: 700;
    font-size: 28px;
    letter-spacing: 1px;
    color: var(--name-slate);
    line-height: 1.1;
  }
  .person-title {
    font-size: 21px;
    line-height: 1.25;
    margin-bottom: 14px;
  }
  .street-address {
    font-size: 21px;
    line-height: 1.3;
    font-style: normal;
    margin-bottom: 14px;
  }
  .contact-list { list-style: none; }
  .contact-item {
    display: flex;
    align-items: center;
    gap: 12px;
    font-size: 20px;
    line-height: 1.55;
  }
  .contact-icon { width: 17px; height: 17px; flex: none; fill: var(--icon-grey); }
</style>
</head>
<body>
  <div class="business-card">
    <section class="brand-panel">
      <p class="brand-name">Quarrystone Development Group, LLC</p>
    </section>
    <section class="contact-panel">
      <h1 class="person-name">ADRIAN VOSSLER</h1>
      <p class="person-title">Founder/CEO</p>
      <address class="street-address">2160 Ledgeview Parkway<br>Fairholt ME 04213</address>
      <ul class="contact-list">
        <li class="contact-item">
          <svg class="contact-icon" viewBox="0 0 24 24" aria-hidden="true"><path d="M6.6 10.8a15.1 15.1 0 0 0 6.6 6.6l2.2-2.2c.3-.3.7-.4 1-.2 1.1.4 2.3.6 3.6.6.6 0 1 .4 1 1V20c0 .6-.4 1-1 1A17 17 0 0 1 3 4c0-.6.4-1 1-1h3.5c.6 0 1 .4 1 1 0 1.3.2 2.5.6 3.6.1.3 0 .7-.2 1z"/></svg>
          (555)-312-0496
        </li>
        <li class="contact-item">
          <svg class="contact-icon" viewBox="0 0 24 24" aria-hidden="true"><path d="M2 5h20v14H2z M3.5 6.5 12 13l8.5-6.5" fill="none" stroke="#5f6470" stroke-width="2"/><path d="M2 5h20L12 12.5z"/></svg>
          info@quarrystonedevelopment.com
        </li>
        <li class="contact-item">
          <svg class="contact-icon" viewBox="0 0 24 24" aria-hidden="true"><circle cx="12" cy="12" r="10" fill="none" stroke="#5f6470" stroke-width="2"/><path d="M2 12h20M12 2c3 3 3 17 0 20M12 2c-3 3-3 17 0 20" fill="none" stroke="#5f6470" stroke-width="1.6"/></svg>
          www.quarrystonedevelopment.com
        </li>
      </ul>
    </section>
  </div>
</body>
</html>
```